Detail Shop Business card design

i need a business card design for my new detailing company called 'Brisk's Polish Works'. i want an all black and white design . simple, direct and to the point. i want the designer to choose a fitting font to match the logothe front should have logo, address, phone and email and the back side should have a slogan and text indicating that we offer services on anything including cars, trucks, motorcycles and RVs. slogan will read "we take pride in your ride"
maybe also very small on the back side the IG icon with Brisks_Polish_Works

phone 208.417.6352
address 3847 E Larkin Ave
Spokane WA 99214
email: BrisksPolish@mailvexo.com

Target Market(s)

all ages , auto enthusiasts

Industry/Entity Type

Automotive

Contact Information for Business Card

the front should have logo, address, phone and email and the back side should have a slogan and text indicating that we offer services on anything including cars, trucks, motorcycles and RVs. slogan will read "we take pride in your ride"

phone 208.417.6352
address 3847 E Larkin Ave
Spokane WA 99214

Colors
000000
ffffff

Requirements
Must have
• bold font and very simple design with good spacing
Nice to have
• anything creative from the designer indicating we service any types of vehicles
Should not have
• any colors ,

```html
<!DOCTYPE html>
<html lang="en">
<head>
<meta charset="utf-8">
<title>Brisk's Polish Works – Business Card</title>
<link href="https://fonts.googleapis.com/css2?family=Open+Sans:ital,wght@0,400;0,600;0,700;0,800;1,400&display=swap" rel="stylesheet">
<style>
  :root {
    --backdrop: #2b2523;
    --card: #0d0d0d;
    --card-edge: #1c1c1c;
    --ink: #ffffff;
    --ink-soft: #d9d9d9;
    --ink-muted: #9a9a9a;
    --silver-light: #e6e6e6;
    --silver-dark: #5e5e5e;
  }
  * { box-sizing: border-box; margin: 0; padding: 0; }
  html, body {
    width: 1200px;
    height: 864px;
    overflow: hidden;
    background: var(--backdrop);
    font-family: "Open Sans", Arial, sans-serif;
    color: var(--ink);
  }
  .stage {
    width: 1200px;
    height: 864px;
    display: flex;
    align-items: center;
    justify-content: center;
    gap: 40px;
  }
  .card {
    position: relative;
    width: 560px;
    height: 320px;
    background: var(--card);
    border: 1px solid var(--card-edge);
    border-radius: 4px;
    box-shadow: 0 14px 30px rgba(0,0,0,0.45);
    overflow: hidden;
  }

  /* Back side */
  .card-back {
    display: flex;
    flex-direction: column;
    align-items: center;
  }
  .hero-vehicle {
    margin-top: 34px;
    width: 300px;
    height: 150px;
    border-radius: 6px;
    background: radial-gradient(ellipse at 50% 55%, var(--silver-light) 0%, #a9a9a9 40%, var(--silver-dark) 75%, rgba(13,13,13,0) 100%);
  }
  .slogan {
    margin-top: 22px;
    font-weight: 800;
    font-size: 19px;
    letter-spacing: 0.5px;
    color: var(--ink-soft);
  }
  .slogan-rule {
    width: 360px;
    height: 1px;
    margin-top: 8px;
    background: var(--ink-muted);
  }
  .services {
    margin-top: 9px;
    font-style: italic;
    font-size: 13px;
    color: var(--ink-muted);
  }

  /* Front side */
  .card-front {
    display: flex;
    align-items: center;
  }
  .brand {
    width: 270px;
    display: flex;
    align-items: center;
    justify-content: center;
    gap: 10px;
    padding-left: 24px;
  }
  .brand-dot {
    width: 16px;
    height: 16px;
    border-radius: 50%;
    background: var(--ink);
    flex: none;
  }
  .brand-name {
    font-weight: 800;
    font-size: 23px;
    line-height: 1.15;
    color: var(--ink);
  }
  .divider {
    width: 1px;
    height: 150px;
    background: linear-gradient(to bottom, rgba(255,255,255,0), var(--ink-soft) 20%, var(--ink-soft) 80%, rgba(255,255,255,0));
  }
  .contact {
    padding-left: 26px;
    font-size: 14px;
    line-height: 1.35;
    color: var(--ink);
  }
  .person-name {
    font-weight: 700;
    font-size: 19px;
    letter-spacing: 0.5px;
  }
  .person-title {
    font-size: 13px;
    letter-spacing: 0.5px;
    margin-bottom: 6px;
  }
  .address { margin-bottom: 6px; }
  .contact-list { list-style: none; }
  .contact-list li {
    display: flex;
    align-items: center;
    gap: 8px;
  }
  .contact-list svg {
    width: 13px;
    height: 13px;
    flex: none;
    fill: var(--ink);
  }
</style>
</head>
<body>
<main class="stage">

  <section class="card card-back" aria-label="Business card back">
    <div class="hero-vehicle" role="img" aria-label="Silver illustration of a classic hot rod car"></div>
    <p class="slogan">WE TAKE PRIDE IN YOUR RIDE</p>
    <div class="slogan-rule"></div>
    <p class="services">we offer services on anything including cars, trucks, motorcycles &amp; RVs</p>
  </section>

  <section class="card card-front" aria-label="Business card front">
    <div class="brand">
      <span class="brand-dot"></span>
      <span class="brand-name">Brisk's<br>Polish Works</span>
    </div>
    <div class="divider"></div>
    <div class="contact">
      <p class="person-name">MARCUS HALE</p>
      <p class="person-title">PRESIDENT</p>
      <p class="address">3847 E Larkin Ave<br>Spokane WA 99214</p>
      <ul class="contact-list">
        <li>
          <svg viewBox="0 0 16 16" aria-hidden="true"><path d="M3 1h3l1.5 3.5-2 1.3a8 8 0 0 0 4.7 4.7l1.3-2L15 10v3a2 2 0 0 1-2 2C6.4 15 1 9.6 1 3a2 2 0 0 1 2-2z"/></svg>
          208.417.6352
        </li>
        <li>
          <svg viewBox="0 0 16 16" aria-hidden="true"><path d="M4 0h8a1 1 0 0 1 1 1v14a1 1 0 0 1-1 1H4a1 1 0 0 1-1-1V1a1 1 0 0 1 1-1zm1 2v10h6V2zm3 11a1 1 0 1 0 0 2 1 1 0 0 0 0-2z"/></svg>
          208 553 7190
        </li>
        <li>
          <svg viewBox="0 0 16 16" aria-hidden="true"><path d="M1 3h14v10H1zm1.5 1.2v.4L8 8.5l5.5-3.9v-.4zM2.5 6.3v5.2h11V6.3L8 10.2z"/></svg>
          BrisksPolish@mailvexo.com
        </li>
        <li>
          <svg viewBox="0 0 16 16" aria-hidden="true"><path d="M8 0a8 8 0 1 0 0 16A8 8 0 0 0 8 0zm0 1.5c.9 0 1.9 1.6 2.3 4H5.7c.4-2.4 1.4-4 2.3-4zM1.6 7h2.9a14 14 0 0 0 0 2H1.6a6.5 6.5 0 0 1 0-2zm4 0h4.8a12 12 0 0 1 0 2H5.6a12 12 0 0 1 0-2zm5.9 0h2.9a6.5 6.5 0 0 1 0 2h-2.9a14 14 0 0 0 0-2zM5.7 10.5h4.6c-.4 2.4-1.4 4-2.3 4s-1.9-1.6-2.3-4z"/></svg>
          www.briskspolishworks.com
        </li>
      </ul>
    </div>
  </section>

</main>
</body>
</html>
```